Business Card Design Project

We need a new fresh business card for our business. There are multiple services we offer and we need a fresh corporate card that represents us better. We start from cleaning carpet and tiles, to upholstery and curtains, to completely clean all contents and building materials after a fire, or completely dry out a home or business after a major or minor flood event. We are open to all concepts as we want to create a new look, maybe even logo, signage, vehicle signage, uniforms.
We are open to new colours etc.

Go to www.brolvaquincare.com.au for current logo and all other past ideas

Target Market(s)

Everyone is our possible client but we are targeting more coorporate

Industry/Entity Type

Building

```html
<!DOCTYPE html>
<html lang="en">
<head>
<meta charset="utf-8">
<title>Brolvaquin Care – Business Card</title>
<link href="https://fonts.googleapis.com/css2?family=Josefin+Sans:wght@400;600;700&display=swap" rel="stylesheet">
<style>
  :root {
    --page-bg: #e9e7e4;
    --card-white: #f7f7f7;
    --card-shade: #e6e6e6;
    --brand-blue: #1a5aa3;
    --brand-pink: #e0177a;
    --text-dark: #3a3a3a;
    --rule-grey: #9a9a9a;
    --ring-grey: #a9adb3;
  }
  * { margin: 0; padding: 0; box-sizing: border-box; }
  html, body { width: 1200px; height: 900px; overflow: hidden; }
  body {
    background: var(--page-bg);
    font-family: "Josefin Sans", sans-serif;
    position: relative;
  }
  .business-card {
    position: absolute;
    left: 75px; top: 150px;
    width: 1050px; height: 600px;
    border-radius: 64px;
    overflow: hidden;
    background: linear-gradient(160deg, var(--card-white) 0%, var(--card-shade) 100%);
    box-shadow: 0 14px 40px rgba(0,0,0,0.18);
  }
  .card-wave { position: absolute; left: 0; top: 0; width: 1050px; height: 600px; }
  .brand-lockup {
    position: absolute;
    left: 420px; top: 78px;
    display: flex; align-items: center; gap: 18px;
  }
  .brand-name {
    font-weight: 700;
    font-size: 40px;
    color: var(--brand-blue);
    letter-spacing: 1px;
  }
  .brand-dot {
    width: 84px; height: 84px;
    border-radius: 50%;
    border: 6px solid var(--ring-grey);
    background: var(--brand-blue);
  }
  .holder-details {
    position: absolute;
    right: 525px; top: 215px;
    text-align: right;
    color: var(--text-dark);
    font-variant: small-caps;
    letter-spacing: 2px;
  }
  .holder-name { font-size: 30px; font-weight: 700; letter-spacing: 3px; }
  .holder-role { font-size: 24px; margin-top: 4px; }
  .holder-address { font-size: 24px; margin-top: 30px; line-height: 1.35; }
  .detail-rule {
    position: absolute;
    left: 545px; top: 210px;
    width: 2px; height: 180px;
    background: var(--rule-grey);
  }
  .contact-list {
    position: absolute;
    left: 565px; top: 218px;
    list-style: none;
    color: var(--text-dark);
    font-size: 24px;
    letter-spacing: 2px;
  }
  .contact-list li { display: flex; align-items: center; gap: 10px; height: 32px; }
  .contact-list li.contact-gap { margin-top: 6px; }
  .contact-list .web-line { font-variant: small-caps; }
  .contact-icon { width: 22px; height: 22px; flex: none; }
</style>
</head>
<body>
  <div class="business-card">
    <svg class="card-wave" viewBox="0 0 1050 600" aria-hidden="true">
      <path d="M0 345 C 200 345, 320 450, 560 458 C 760 466, 900 476, 1050 512 L1050 600 L0 600 Z" fill="var(--brand-pink)"/>
      <path d="M0 385 C 200 385, 320 478, 560 486 C 760 492, 900 504, 1050 532 L1050 600 L0 600 Z" fill="#ffffff"/>
      <path d="M0 397 C 200 402, 320 494, 560 500 C 760 505, 900 515, 1050 540 L1050 600 L0 600 Z" fill="var(--brand-blue)"/>
    </svg>

    <div class="brand-lockup">
      <span class="brand-name">Brolvaquin Care</span>
      <span class="brand-dot"></span>
    </div>

    <div class="holder-details">
      <div class="holder-name">Dorian Velkamp</div>
      <div class="holder-role">Owner / C.E.O</div>
      <div class="holder-address">Suite # 118, Orvel House,<br>NSW 2914</div>
    </div>

    <div class="detail-rule"></div>

    <ul class="contact-list">
      <li>
        <svg class="contact-icon" viewBox="0 0 22 22" aria-hidden="true"><circle cx="11" cy="11" r="11" fill="var(--text-dark)"/><path d="M7 6 L9 6 L10 9 L8.6 10 C9.3 11.6 10.4 12.7 12 13.4 L13 12 L16 13 L16 15 C11 15.5 6.5 11 7 6 Z" fill="#fff"/></svg>
        555-210-4481
      </li>
      <li>
        <svg class="contact-icon" viewBox="0 0 22 22" aria-hidden="true"><circle cx="11" cy="11" r="11" fill="var(--text-dark)"/><rect x="7.5" y="4.5" width="7" height="13" rx="1.5" fill="#fff"/><rect x="8.8" y="6.5" width="4.4" height="7" fill="var(--text-dark)"/></svg>
        555-738-1902
      </li>
      <li>
        <svg class="contact-icon" viewBox="0 0 22 22" aria-hidden="true"><circle cx="11" cy="11" r="11" fill="var(--text-dark)"/><rect x="6" y="9" width="10" height="7" fill="#fff"/><rect x="8" y="5" width="6" height="4" fill="#fff"/></svg>
        555-644-2073
      </li>
      <li class="contact-gap">
        <svg class="contact-icon" viewBox="0 0 22 22" aria-hidden="true"><circle cx="11" cy="11" r="11" fill="var(--text-dark)"/><rect x="5.5" y="7" width="11" height="8" fill="#fff"/><path d="M5.5 7 L11 11.5 L16.5 7" fill="none" stroke="var(--text-dark)" stroke-width="1.2"/></svg>
        info@brolvaquincare.com.au
      </li>
      <li>
        <svg class="contact-icon" viewBox="0 0 22 22" aria-hidden="true"><circle cx="11" cy="11" r="11" fill="var(--text-dark)"/><circle cx="11" cy="11" r="6" fill="none" stroke="#fff" stroke-width="1.4"/><ellipse cx="11" cy="11" rx="2.6" ry="6" fill="none" stroke="#fff" stroke-width="1.2"/><line x1="5" y1="11" x2="17" y2="11" stroke="#fff" stroke-width="1.2"/></svg>
        <span class="web-line">www.brolvaquincare.com.au</span>
      </li>
    </ul>
  </div>
</body>
</html>
```